Banner ads for LP that work with same theme as below banners

Love the banner ads below. Need more with attached photos. But use the same wording, font as in below banner ads. Should be LP size 1200/627 so I can use for Pixorly and LP. Looking for great ads to use as LP ads. We do lots of ads so it will be worth your time to enter this contest you will be rewarded with a ton of work. Need several banner ads that work together. So maybe 1 of the dresses, 1 of the sweater, 1 of the leggings, 1 of the jacket

Target Market(s)

Women 24-45

Industry/Entity Type

Fashion

Requirements
Must have
• Banner ads that work for LP and Pixorly
Nice to have
• Several options to choose from
Should not have
• not sure

```html
<!DOCTYPE html>
<html lang="en">
<head>
<meta charset="utf-8">
<title>Our Best Dresses Ever – Banner</title>
<link rel="stylesheet" href="https://fonts.googleapis.com/css2?family=Rochester&family=Playfair+Display:wght@700&display=block">
<style>
  :root {
    --sky-top: #bfe3f0;
    --sky-mid: #e9dbe6;
    --horizon-pink: #f1c4cf;
    --city-mauve: #a98a99;
    --city-deep: #7d6270;
    --frame-white: #ffffff;
    --headline-maroon: #5e1414;
    --button-ink: #1a1214;
    --photo-hair: #b8875a;
    --photo-dark: #2e2634;
    --photo-blue: #3a5398;
    --photo-sky: #d8e6ee;
  }
  * { margin: 0; padding: 0; box-sizing: border-box; }
  html, body { width: 1200px; height: 628px; overflow: hidden; background: #ffffff; }
  .banner {
    position: relative;
    width: 1200px;
    height: 628px;
    overflow: hidden;
  }
  .city-backdrop {
    position: absolute;
    inset: 0;
    background: linear-gradient(180deg, var(--sky-top) 0%, #d6ecf4 28%, var(--sky-mid) 45%, var(--horizon-pink) 55%, var(--city-mauve) 72%, var(--city-deep) 100%);
  }
  .light-facets { position: absolute; inset: 0; }
  .outer-frame {
    position: absolute;
    left: 18px;
    top: 18px;
    width: 1162px;
    height: 592px;
    border: 2px solid var(--frame-white);
  }
  .model-panel {
    position: absolute;
    left: 678px;
    top: 0;
    width: 368px;
    height: 628px;
    background: rgba(255, 255, 255, 0.55);
    box-shadow: 0 0 24px rgba(60, 50, 70, 0.35);
  }
  .model-photo {
    position: absolute;
    left: 703px;
    top: 28px;
    width: 320px;
    height: 592px;
    background:
      linear-gradient(90deg, rgba(216, 230, 238, 0.55) 0%, rgba(216, 230, 238, 0) 22%, rgba(216, 230, 238, 0) 85%, rgba(216, 230, 238, 0.5) 100%),
      linear-gradient(180deg, var(--photo-hair) 0%, #a9876c 22%, var(--photo-dark) 38%, var(--photo-blue) 62%, var(--photo-dark) 88%, #b99a86 100%);
  }
  .headline {
    position: absolute;
    left: 230px;
    top: 44px;
    width: 360px;
    text-align: center;
    color: var(--headline-maroon);
    font-weight: 400;
  }
  .headline .script {
    display: block;
    font-family: "Rochester", cursive;
    font-size: 88px;
    line-height: 1;
  }
  .headline .caps {
    display: block;
    font-family: "Playfair Display", serif;
    font-weight: 700;
    font-size: 50px;
    letter-spacing: 13px;
    line-height: 1.2;
    margin: 0 0 0 13px;
  }
  .shop-button {
    position: absolute;
    left: 234px;
    top: 365px;
    width: 343px;
    height: 62px;
    border: 2px solid var(--frame-white);
    background: rgba(255, 255, 255, 0.35);
    display: flex;
    align-items: center;
    justify-content: center;
    font-family: "Playfair Display", serif;
    font-weight: 700;
    font-size: 30px;
    color: var(--button-ink);
    text-decoration: none;
  }
</style>
</head>
<body>
  <main class="banner">
    <div class="city-backdrop" role="img" aria-label="Aerial photo of a city skyline under a pastel blue and pink sky"></div>
    <svg class="light-facets" width="1200" height="628" viewBox="0 0 1200 628" aria-hidden="true">
      <polygon points="0,180 140,628 0,628" fill="#ffffff" opacity="0.18"/>
      <polygon points="0,0 220,0 40,628 0,628" fill="#ffffff" opacity="0.12"/>
      <polygon points="1200,160 1060,628 1200,628" fill="#ffffff" opacity="0.18"/>
      <polygon points="1200,0 1000,0 1160,628 1200,628" fill="#ffffff" opacity="0.12"/>
    </svg>
    <div class="outer-frame"></div>
    <div class="model-panel"></div>
    <div class="model-photo" role="img" aria-label="Photo of a woman with long wavy hair wearing a dark floral lace mini dress with blue flowers"></div>
    <h1 class="headline">
      <span class="script">Our Best</span>
      <span class="caps">DRESSES</span>
      <span class="script">Ever!</span>
    </h1>
    <a class="shop-button" href="#">SHOP THE LOOK</a>
  </main>
</body>
</html>
```